VTMB site redesign

Please redesign a home page with content provided. PSD only - no coding
Can use any images from Snapwelder.com

Please create a site design that more clearly illustrates the client's services and expertise. We are looking for a high-end design.

Any images used must be generic or of Dallas TX.

Fonts: Any
Colors: Match to logo
Look: Modern - Professional

Target Market(s)

medium-large business owners

Number of Pages Required

1 page

Font styles to use
Serif
Sans Serif

Requirements
Must have
• cohesive professional design
• high end look
• Match to logo

```html
<!DOCTYPE html>
<html lang="en">
<head>
<meta charset="utf-8">
<title>VTMB – Dallas Commercial Realty</title>
<link href="https://fonts.googleapis.com/css2?family=Cormorant+Garamond:ital,wght@0,600;0,700;1,500;1,600&family=Lato:ital,wght@0,400;0,700;1,400&display=swap" rel="stylesheet">
<style>
:root{
  --red:#a50f14;
  --red-dark:#7e0a0e;
  --ink:#333333;
  --muted:#7a7a7a;
  --light:#f0f0f0;
  --topbar:#2b2b2b;
  --footer:#2f2f2f;
  --bottom:#222222;
  --white:#ffffff;
  --serif:'Cormorant Garamond', Georgia, serif;
  --sans:'Lato', Arial, sans-serif;
}
*{box-sizing:border-box;margin:0;padding:0}
html,body{width:1200px;height:3358px;overflow:hidden}
body{font-family:var(--sans);color:var(--ink);background:var(--white);position:relative}
section,header,footer,.topbar{position:relative;width:1200px}
.abs{position:absolute}
.center{left:0;right:0;text-align:center}
.h2{font-family:var(--serif);font-weight:700;color:var(--red);font-size:44px;letter-spacing:.5px;text-transform:uppercase}

.topbar{height:40px;background:var(--topbar);color:var(--white);font-size:15px}
.topbar .call{left:78px;top:11px;display:flex;align-items:center;gap:10px}
.topbar .social{right:78px;top:13px;display:flex;gap:14px}
.topbar .social span{width:14px;height:14px;border-radius:50%;background:var(--white)}

header{height:144px;background:var(--white)}
.brand{left:78px;top:22px;display:flex;align-items:center;gap:12px}
.brand .mark{width:40px;height:40px;background:var(--red)}
.brand .name{font-family:var(--serif);font-weight:700;font-size:56px;color:var(--red);line-height:1}
.tagline{right:80px;top:32px;font-size:20px;font-weight:700;color:#555;letter-spacing:.3px}
nav{right:80px;top:92px;display:flex;gap:38px;font-size:15px;color:#555;text-transform:uppercase}
nav .active{color:var(--red)}

.hero{height:562px}
.hero .photo{inset:0;background:linear-gradient(100deg,#3a3d40 0%,#55595c 45%,#2f3235 100%)}
.hero .frame{left:347px;top:136px;width:515px;height:289px;border:12px solid rgba(255,255,255,.35)}
.hero h1{top:228px;font-family:var(--serif);font-weight:600;color:var(--white);font-size:46px;line-height:58px;letter-spacing:.5px}

.welcome{height:369px}
.welcome .h2{top:46px}
.welcome .lede{top:100px;font-style:italic;font-size:18px;color:#555}
.welcome p.body{left:188px;width:824px;top:140px;font-size:14px;line-height:20px;color:#666;text-align:center}
.btn{display:block;background:var(--red);color:var(--white);font-family:var(--serif);font-weight:700;font-size:22px;text-align:center;letter-spacing:.5px;outline:2px solid var(--red);outline-offset:3px;border:1px solid var(--white)}
.welcome .btn{left:506px;top:257px;width:188px;height:45px;line-height:43px}

.why{height:481px;background:var(--light)}
.why .h2{top:48px}
.cards{left:78px;top:114px;display:flex;gap:31px}
.card{width:238px;height:291px;background:var(--white);border-bottom:5px solid var(--red);text-align:center;padding-top:46px}
.card svg{width:86px;height:80px}
.card h3{font-weight:400;font-size:22px;color:#444;margin-top:22px}
.card p{font-size:14px;line-height:24px;color:#888;margin:10px 22px 0}

.banner{height:249px}
.banner .photo{inset:0;background:linear-gradient(110deg,#1b2838 0%,#2c4460 50%,#1a2433 100%)}
.banner p{top:48px;font-family:var(--serif);font-style:italic;font-weight:500;color:var(--white);font-size:32px;line-height:40px}
.banner .btn{left:466px;top:148px;width:266px;height:43px;line-height:41px}

.team{height:448px}
.team .h2{top:60px}
.team p.body{left:200px;width:800px;top:118px;font-size:14px;line-height:19px;color:#666;text-align:center}
.member{top:248px;display:flex;gap:38px}
.member .pic{width:103px;height:110px}
.member .who{padding-top:16px}
.member h4{font-weight:400;font-size:19px;color:#444;line-height:24px}
.member .rule{width:36px;height:3px;background:var(--red);margin:12px 0 14px}
.member span{font-size:15px;color:#666}

.testimonial{height:304px;background:var(--light)}
.testimonial h2{left:134px;top:104px;line-height:52px;text-align:left}
.testimonial .divider{left:392px;top:62px;width:1px;height:175px;background:#cfcfcf}
.testimonial .pic{left:432px;top:89px;width:125px;height:125px;background:linear-gradient(135deg,#c9c4bd,#7f868e)}
.testimonial blockquote{left:582px;top:120px;width:520px;font-style:italic;font-size:14px;line-height:25px;color:#777}
.testimonial cite{left:582px;top:180px;font-style:normal;font-size:14px;font-weight:700;color:#555}

.articles{height:343px}
.articles .h2{top:50px}
.post{top:110px;width:500px;height:156px;border:1px solid #ddd;background:var(--white);display:flex}
.post .pic{width:249px;height:154px}
.post .txt{padding:20px 0 0 24px;width:250px}
.post time{font-size:15px;color:#666}
.post .rule{width:36px;height:3px;background:var(--red);margin:12px 0 10px}
.post p{font-size:14px;line-height:25px;color:#777}

footer{height:228px;background:var(--footer);color:var(--white)}
footer .brand{top:70px}
footer .brand .name{color:var(--white)}
footer .brand .mark{background:var(--red)}
.contact{left:857px;top:66px;font-size:15px;line-height:22px}
.contact li{list-style:none;display:flex;gap:18px;align-items:flex-start;margin-bottom:12px}
.contact svg{width:18px;height:18px;flex:none;margin-top:2px}

.legal{height:190px;background:var(--bottom);color:#eee;text-align:center;font-size:14px;line-height:27px;padding-top:38px}
.legal a{color:var(--red);text-decoration:underline;display:block}
</style>
</head>
<body>

<div class="topbar">
  <div class="abs call">Call Us Today!
    <svg width="16" height="16" viewBox="0 0 24 24" fill="#fff" aria-hidden="true"><path d="M6.6 10.8a15.1 15.1 0 0 0 6.6 6.6l2.2-2.2c.3-.3.7-.4 1-.2 1.1.4 2.3.6 3.6.6.6 0 1 .4 1 1V20c0 .6-.4 1-1 1A17 17 0 0 1 3 4c0-.6.4-1 1-1h3.5c.6 0 1 .4 1 1 0 1.3.2 2.5.6 3.6.1.3 0 .7-.2 1z"/></svg>
    214-555-0143</div>
  <div class="abs social" aria-label="Social links"><span></span><span></span><span></span></div>
</div>

<header>
  <div class="abs brand"><span class="mark"></span><span class="name">VTMB</span></div>
  <div class="abs tagline">PROFESSIONAL OFFICE AND WAREHOUSE LEASING</div>
  <nav class="abs"><span class="active">Home</span><span>Services</span><span>About VTMB</span><span>Market News</span><span>Blog</span><span>Contact</span></nav>
</header>

<section class="hero">
  <div class="abs photo" role="img" aria-label="Business people walking through a glass office lobby"></div>
  <div class="abs frame"></div>
  <h1 class="abs center">DALLAS COMMERICAL<br>REALTY since 1982</h1>
</section>

<section class="welcome">
  <h2 class="abs center h2">Welcome to VTMB</h2>
  <div class="abs center lede">Fast-track your search with tenant reps that only serve you, and specialize in the DFW area.</div>
  <p class="abs body">At VTMB, we focus solely on office and industrial/warehouse commercial real estate leasing and sales in the greater Dallas/Fort Worth area. We believe that our unique commercial office space service and market knowledge is the key to our clients' growth and ultimate business success. We strive to learn the specific needs of your company and be an essential team member that will find the best solution for your commercial real estate needs.</p>
  <a class="abs btn">READ MORE</a>
</section>

<section class="why">
  <h2 class="abs center h2">Why Tenant Representation?</h2>
  <div class="abs cards">
    <div class="card">
      <svg viewBox="0 0 86 80" aria-hidden="true"><path fill="#a50f14" d="M43 76 8 42A20 20 0 0 1 43 14a20 20 0 0 1 35 28z"/><path d="M24 44l12-10 10 8 12-10" stroke="#fff" stroke-width="4" fill="none" stroke-linecap="round"/></svg>
      <h3>Relationships</h3>
      <p>Save time by trusting VTMB year after year to find the right location for you.</p>
    </div>
    <div class="card">
      <svg viewBox="0 0 86 80" aria-hidden="true"><circle cx="62" cy="24" r="10" fill="#a50f14"/><path fill="#a50f14" d="M6 46h14l16 6h18a5 5 0 0 1 0 10H38v2h20l18-10a5 5 0 0 1 6 8L60 74H20l-14-4z"/><path d="M30 22h18M34 30h16" stroke="#a50f14" stroke-width="4" stroke-linecap="round"/></svg>
      <h3>Access to More</h3>
      <p>We have no agreements or personal incentives for specific properties.</p>
    </div>
    <div class="card">
      <svg viewBox="0 0 86 80" aria-hidden="true"><circle cx="43" cy="40" r="34" fill="none" stroke="#a50f14" stroke-width="6"/><line x1="19" y1="16" x2="67" y2="64" stroke="#a50f14" stroke-width="6"/><text x="43" y="54" text-anchor="middle" font-family="Lato, sans-serif" font-weight="700" font-size="40" fill="#a50f14">$</text></svg>
      <h3>Free To You</h3>
      <p>You pay us nothing. We get our commission from the property being leased.</p>
    </div>
    <div class="card">
      <svg viewBox="0 0 86 80" aria-hidden="true"><circle cx="43" cy="16" r="12" fill="#a50f14"/><path fill="#a50f14" d="M25 56c0-14 8-24 18-24s18 10 18 24z"/><path fill="#a50f14" d="M4 56h18l10 6h30l16-8a4 4 0 0 1 4 7L62 74H16L4 68z"/></svg>
      <h3>Customized Service</h3>
      <p>Aside from saving you the time of repeating what your needs are to each new location.</p>
    </div>
  </div>
</section>

<section class="banner">
  <div class="abs photo" role="img" aria-label="Glass office towers seen from below against the sky"></div>
  <p class="abs center">If you need to find office or warehouse space in the Dallas Fort Worth<br>area, the team at VTMB has the experience you need.</p>
  <a class="abs btn">SPACE CALCULATOR</a>
</section>

<section class="team">
  <h2 class="abs center h2">Meet the Team</h2>
  <p class="abs body">At VTMB we believe that you deserve the best professional advice and personal service with your commercial real estate negotiations. By choosing VTMB as your tenant reps in the Dallas/Fort Worth area, you will receive the assistance of accomplished and experienced commercial real estate brokers and salespeople who are licensed by the State Real Estate Commission to practice in Texas since 1982.</p>
  <div class="abs member" style="left:78px">
    <div class="pic" role="img" aria-label="Portrait of Warren D. Ashby" style="background:linear-gradient(160deg,#8a6f5c,#2a2d35)"></div>
    <div class="who"><h4>Warren D. Ashby</h4><div class="rule"></div><span>Founder and President</span></div>
  </div>
  <div class="abs member" style="left:439px">
    <div class="pic" role="img" aria-label="Portrait of Neil Hartwell-Cole" style="background:linear-gradient(160deg,#6f6a66,#26282d)"></div>
    <div class="who"><h4>Neil Hartwell-Cole</h4><div class="rule"></div><span>Senior Director</span></div>
  </div>
  <div class="abs member" style="left:801px">
    <div class="pic" role="img" aria-label="Portrait of Daniel Joseph Crane" style="background:linear-gradient(160deg,#d9744a,#9aa0a8)"></div>
    <div class="who" style="padding-top:6px"><h4>Daniel Joseph<br>Crane</h4><div class="rule"></div><span>Jr., Associate</span></div>
  </div>
</section>

<section class="testimonial">
  <h2 class="abs h2">What Our<br>Client Say</h2>
  <div class="abs divider"></div>
  <div class="abs pic" role="img" aria-label="Portrait of a client in a suit"></div>
  <blockquote class="abs">Lorem Ipsum is simply dummy text of the printing and typesetting industry. Lorem Ipsum has been the industry's standard dummy text ever.</blockquote>
  <cite class="abs">-NAME SURNAME</cite>
</section>

<section class="articles">
  <h2 class="abs center h2">Recent Articles</h2>
  <article class="abs post" style="left:78px">
    <div class="pic" role="img" aria-label="Laptop on a desk with warm light" style="background:linear-gradient(120deg,#e39a4a,#4a4f58)"></div>
    <div class="txt"><time>March 10, 2018</time><div class="rule"></div><p>Lorem Ipsum is simply dummy text of the printing and types industry. Lorem Ipsum has bn.</p></div>
  </article>
  <article class="abs post" style="left:622px">
    <div class="pic" role="img" aria-label="Colleagues meeting around a table" style="background:linear-gradient(120deg,#c9c5c0,#6d6a66)"></div>
    <div class="txt"><time>March 10, 2018</time><div class="rule"></div><p>Lorem Ipsum is simply dummy text of the printing and types industry. Lorem Ipsum has bn.</p></div>
  </article>
</section>

<footer>
  <div class="abs brand"><span class="mark"></span><span class="name">VTMB</span></div>
  <ul class="abs contact">
    <li><svg viewBox="0 0 24 24" fill="#fff" aria-hidden="true"><path d="M12 2a7 7 0 0 0-7 7c0 5 7 13 7 13s7-8 7-13a7 7 0 0 0-7-7zm0 9.5A2.5 2.5 0 1 1 12 6.5a2.5 2.5 0 0 1 0 5z"/></svg><span>4120 Cedar Bend Avenue, Suite<br>620, Dallas, TX 75219</span></li>
    <li><svg viewBox="0 0 24 24" fill="#fff" aria-hidden="true"><path d="M6.6 10.8a15.1 15.1 0 0 0 6.6 6.6l2.2-2.2c.3-.3.7-.4 1-.2 1.1.4 2.3.6 3.6.6.6 0 1 .4 1 1V20c0 .6-.4 1-1 1A17 17 0 0 1 3 4c0-.6.4-1 1-1h3.5c.6 0 1 .4 1 1 0 1.3.2 2.5.6 3.6.1.3 0 .7-.2 1z"/></svg><span>214-555-0143</span></li>
    <li><svg viewBox="0 0 24 24" fill="#fff" aria-hidden="true"><rect x="3" y="8" width="18" height="12" rx="1"/><rect x="7" y="3" width="10" height="6" fill="none" stroke="#fff" stroke-width="2"/><rect x="7" y="12" width="10" height="2" fill="#2f2f2f"/></svg><span>214-555-0188</span></li>
  </ul>
</footer>

<div class="legal">
  State Real Estate Commission Mandated Disclosure Notices – click links below to view pages
  <a>State Real Estate Commission Information About Brokerage Services</a>
  <a>State Real Estate Commission Consumer Protection Notice</a>
  2018 ©VALTMORE COMMERCIAL BROKERS . All Rights Reserved.
</div>

</body>
</html>
```